Road Construction Company needs business cards

We would like a new business card designed for our business.

We're a road construction company based in Qld, Australia.

Can the business card please have the following information on it.

Name: Warren Halbeck
Position: General Manager
Phone: 0472 915 348
Email: Warren.halbeck@tovrin.com.au
Address: 87 Marrow Ave, Pendlebay, QLD, 4023
Website: www.tovrin.com.au

Visually we'd like the card to be professional and simple.

Attached is our logo.

Our website is www.tovrin.com.au

Target Market(s)

Men aged 25-60

Contact Information for Business Card

As listed in project description

Font styles to use
Serif

Requirements
Must have
• Large logo on back of card

```html
<!DOCTYPE html>
<html lang="en">
<head>
<meta charset="utf-8">
<title>Tovrin Business Card</title>
<link rel="stylesheet" href="https://fonts.googleapis.com/css2?family=Montserrat:wght@400;500;600;800&display=swap">
<style>
  :root {
    --brand-dark: #0d56a6;
    --brand-light: #32a7dc;
    --ink: #222428;
    --paper: #ffffff;
    --backdrop: #3a3b3d;
  }
  * { box-sizing: border-box; margin: 0; padding: 0; }
  html, body {
    width: 1200px; height: 1059px; overflow: hidden;
    background: var(--backdrop);
    font-family: "Montserrat", Arial, sans-serif;
  }
  .card {
    position: absolute;
    width: 690px; height: 392px;
    border-radius: 18px;
    overflow: hidden;
  }
  .card-front { left: 256px; top: 100px; background: var(--paper); }
  .card-back { left: 254px; top: 537px; height: 394px; background: var(--brand-dark);
    display: flex; align-items: center; justify-content: center; }

  .wordmark {
    font-weight: 800;
    color: var(--brand-dark);
    letter-spacing: 0.02em;
    line-height: 1;
  }
  .card-front .wordmark {
    position: absolute; left: 40px; top: 170px; width: 274px;
    text-align: center; font-size: 50px;
  }
  .card-back .wordmark { color: var(--paper); font-size: 84px; }

  .divider {
    position: absolute; left: 344px; top: 101px;
    width: 2px; height: 190px; background: var(--brand-dark);
  }
  .details { position: absolute; left: 374px; top: 96px; color: var(--ink); }
  .name { font-size: 30px; font-weight: 600; line-height: 1; color: var(--brand-dark); }
  .name .surname { color: var(--brand-light); }
  .role { font-size: 17px; font-weight: 400; margin-top: 4px; }
  .address { font-size: 16px; line-height: 20px; margin-top: 20px; }
  .contacts { list-style: none; margin-top: 18px; }
  .contacts li { display: flex; align-items: center; font-size: 16px; height: 25px; }
  .contacts svg { width: 13px; height: 13px; margin-right: 8px; fill: var(--brand-dark); flex: none; }

  .base-band { position: absolute; left: 0; bottom: 0; width: 100%; height: 13px; }
</style>
</head>
<body>
  <section class="card card-front">
    <div class="wordmark">TOVRIN</div>
    <div class="divider"></div>
    <div class="details">
      <h1 class="name">Warren <span class="surname">Halbeck</span></h1>
      <p class="role">General Manager</p>
      <p class="address">87 Marrow Ave,<br>Pendlebay, QLD, 4023</p>
      <ul class="contacts">
        <li><svg viewBox="0 0 16 16"><path d="M3.6 1.2l2.2 2.9-1.3 1.6c.9 2 2.4 3.5 4.4 4.5l1.6-1.3 2.9 2.2-1 2.5C7.300 13.300 2.700 8.700 1.1 2.200z"/></svg>0472 915 348</li>
        <li><svg viewBox="0 0 16 16"><path d="M1 3h14v2L8 9 1 5z"/><path d="M1 6.5l7 4 7-4V13H1z"/></svg>Warren.halbeck@tovrin.com.au</li>
        <li><svg viewBox="0 0 16 16"><path d="M8 1a7 7 0 100 14A7 7 0 008 1zm0 1.3c.9.8 1.6 2.2 1.9 3.7H6.1C6.400 4.500 7.100 3.100 8 2.300zM2.400 9.300a5.800 5.800 0 010-2.600h2.500a11 11 0 000 2.600zm.5 1.300h2.200c.3 1.200.7 2.200 1.300 3a5.700 5.700 0 01-3.500-3zM5.100 5.400H2.900a5.700 5.700 0 013.500-3c-.6.800-1 1.800-1.300 3zM8 13.700c-.9-.8-1.600-2.100-1.900-3.100h3.800c-.3 1-1 2.300-1.900 3.100zm2.200-4.400H5.800a9.600 9.600 0 010-2.600h4.400a9.600 9.600 0 010 2.600zm-.6 4.300c.6-.8 1-1.800 1.300-3h2.200a5.700 5.700 0 01-3.500 3zm1.500-4.300a11 11 0 000-2.600h2.500a5.800 5.800 0 010 2.600zm-.2-3.900c-.3-1.200-.7-2.200-1.300-3a5.700 5.700 0 013.500 3z"/></svg>www.tovrin.com.au</li>
      </ul>
    </div>
    <svg class="base-band" viewBox="0 0 690 13" preserveAspectRatio="none" aria-hidden="true">
      <polygon points="0,0 340,0 327,13 0,13" fill="var(--brand-dark)"/>
      <polygon points="353,0 690,0 690,13 340,13" fill="var(--brand-light)"/>
    </svg>
  </section>

  <section class="card card-back">
    <div class="wordmark">TOVRIN</div>
  </section>
</body>
</html>
```